Business Card - connecting 2 souls and beggining the journey of self discovery

Logo on the front
with tag line

On the back list of services and contact details

Seminars
workshops
Coaching
podcasts

Darren Whitlow
Health & Wellbeing Life Coach
0491 372 615
darren@brightcoreliving.example
brightcoreliving.example

Industry/Entity Type

Life Coaching

Contact Information for Business Card

I like the use of colour from the logo to be used. I'm not a fan of white.

Requirements
Must have
• My tagline: The journey home starts with you
Nice to have
• Use of colour that is in the mind body soul logo

```html
<!DOCTYPE html>
<html lang="en">
<head>
<meta charset="utf-8">
<title>Brightcore Living – Business Card</title>
<link rel="stylesheet" href="https://fonts.googleapis.com/css2?family=Open+Sans:wght@400;600;700&display=swap">
<style>
  :root {
    --backdrop: #2b2724;
    --card: #1b1b1d;
    --card-edge: #262628;
    --brand-grey: #6e6e73;
    --soft-grey: #8a8a8f;
    --text-light: #e9e9ea;
    --accent-green: #4cc08e;
    --accent-pink: #e3516b;
    --mark: #5fae8c;
  }
  * { box-sizing: border-box; margin: 0; padding: 0; }
  html, body {
    width: 1200px; height: 864px; overflow: hidden;
    background: var(--backdrop);
    font-family: "Open Sans", Arial, sans-serif;
  }
  .canvas { position: relative; width: 1200px; height: 864px; }
  .card {
    position: absolute; width: 540px; height: 300px;
    background: var(--card);
    border: 1px solid var(--card-edge);
    border-radius: 3px;
    box-shadow: 0 10px 30px rgba(0,0,0,.45);
  }
  .card--services { left: 40px; top: 130px; }
  .card--contact { left: 620px; top: 434px; }

  .brand { display: flex; flex-direction: column; align-items: center; }
  .brand__mark {
    width: 62px; height: 62px; border-radius: 50%;
    background: var(--mark);
  }
  .brand__name {
    color: var(--brand-grey); font-weight: 600;
    letter-spacing: -0.5px; white-space: nowrap;
  }

  .card--services .brand {
    position: absolute; left: 0; right: 0; top: 70px;
  }
  .card--services .brand__name { font-size: 30px; margin-top: 10px; }
  .services {
    position: absolute; left: 30px; bottom: 30px;
    list-style: none; display: flex; gap: 8px;
    color: var(--soft-grey); font-size: 15px;
  }
  .services li + li::before {
    content: ""; display: inline-block; width: 5px; height: 5px;
    border-radius: 50%; background: var(--accent-green);
    margin-right: 8px; vertical-align: middle;
  }

  .card--contact .brand {
    position: absolute; left: 22px; top: 78px; width: 220px;
  }
  .card--contact .brand__mark { width: 52px; height: 52px; }
  .card--contact .brand__name { font-size: 23px; margin-top: 8px; }
  .tagline {
    color: var(--brand-grey); font-size: 12px; font-weight: 600;
    margin-top: 2px; white-space: nowrap;
  }
  .divider {
    position: absolute; left: 258px; top: 50px;
    width: 1px; height: 200px; background: #4a4a4e;
  }
  .contact { position: absolute; left: 282px; top: 94px; }
  .contact__name {
    color: var(--accent-green); font-size: 18px; font-weight: 700;
    text-transform: uppercase; letter-spacing: .3px;
  }
  .contact__role {
    color: var(--accent-pink); font-size: 14px; font-weight: 700;
    text-transform: uppercase; margin-bottom: 10px;
  }
  .contact__list { list-style: none; }
  .contact__list li {
    display: flex; align-items: center; gap: 8px;
    color: var(--text-light); font-size: 13px; line-height: 22px;
  }
  .contact__list svg { width: 12px; height: 12px; fill: var(--accent-green); flex: none; }
</style>
</head>
<body>
<main class="canvas">

  <section class="card card--services" aria-label="Card front">
    <div class="brand">
      <span class="brand__mark"></span>
      <span class="brand__name">Brightcore Living</span>
    </div>
    <ul class="services">
      <li>Seminars</li>
      <li>Workshops</li>
      <li>Coaching</li>
      <li>Podcasts</li>
    </ul>
  </section>

  <section class="card card--contact" aria-label="Card back">
    <div class="brand">
      <span class="brand__mark"></span>
      <span class="brand__name">Brightcore Living</span>
      <span class="tagline">The journey home starts with you</span>
    </div>
    <span class="divider"></span>
    <div class="contact">
      <p class="contact__name">Darren Whitlow</p>
      <p class="contact__role">Health &amp; Wellbeing Life Coach</p>
      <ul class="contact__list">
        <li>
          <svg viewBox="0 0 24 24" aria-hidden="true"><path d="M6.6 10.8a15.1 15.1 0 0 0 6.6 6.6l2.2-2.2a1 1 0 0 1 1-.25 11.4 11.4 0 0 0 3.6.57 1 1 0 0 1 1 1V20a1 1 0 0 1-1 1A17 17 0 0 1 3 4a1 1 0 0 1 1-1h3.5a1 1 0 0 1 1 1c0 1.25.2 2.45.57 3.57a1 1 0 0 1-.25 1z"/></svg>
          0491 372 615
        </li>
        <li>
          <svg viewBox="0 0 24 24" aria-hidden="true"><path d="M2 5h20v14H2z M2 5l10 8 10-8" /></svg>
          darren@brightcoreliving.example
        </li>
        <li>
          <svg viewBox="0 0 24 24" aria-hidden="true"><path d="M12 2a7 7 0 0 0-7 7c0 5.2 7 13 7 13s7-7.8 7-13a7 7 0 0 0-7-7zm0 9.5A2.5 2.5 0 1 1 12 6.5a2.5 2.5 0 0 1 0 5z"/></svg>
          www.brightcoreliving.example
        </li>
      </ul>
    </div>
  </section>

</main>
</body>
</html>
```